Brightway Haul & Upkeep Services, are a company that offers a 'one stop shop' pre-move clean up a

I have already selected a logo which I would like on the front of the business cards along with phone numbers, web address and email which are:
0487650392
www.brightwayhaul.com.au
brightwayhaulandupkeep@mailbox.example

On the back of the card I would like to list some of the types of service we offer (clean - move - repairs/maintenance) which are:
CLEAN - windows, gutters, solar panels, driveways/paths, carpets.
MOVE - Small/medium size house/office moves, large item pick-up & delivery, yard clean-up and removal.
General maintenance and repairs.

I would like the blue logo on a gray background.

Thanks

```html
<!DOCTYPE html>
<html lang="en">
<head>
<meta charset="utf-8">
<title>Brightway Haul &amp; Upkeep Services – Business Card</title>
<link rel="stylesheet" href="https://fonts.googleapis.com/css2?family=Open+Sans:wght@400;600;700&display=swap">
<style>
  :root {
    --page-bg: #e9e9ea;
    --card-light: #f1f1f2;
    --card-mid: #d9dadb;
    --card-dark: #c4c5c7;
    --brand-blue: #2a78c2;
    --brand-deep: #1f5f9e;
    --ink: #2b2b2d;
    --white: #ffffff;
  }
  * { box-sizing: border-box; margin: 0; padding: 0; }
  html, body {
    width: 1200px; height: 788px; overflow: hidden;
    background: var(--page-bg);
    font-family: "Open Sans", sans-serif;
    color: var(--ink);
  }
  .sheet {
    width: 1200px; height: 788px;
    display: flex; align-items: center; justify-content: center; gap: 50px;
  }
  .card {
    position: relative;
    width: 540px; height: 310px;
    overflow: hidden;
    background: radial-gradient(ellipse at 30% 55%, var(--card-light) 0%, var(--card-mid) 60%, var(--card-dark) 100%);
    box-shadow: 0 6px 18px rgba(0,0,0,0.18);
  }

  /* Brand name block */
  .brand {
    display: flex; align-items: center; gap: 10px;
    color: var(--brand-blue);
    font-weight: 700;
    line-height: 1.05;
  }
  .brand-square { flex: none; background: var(--brand-blue); }

  /* Front */
  .card-front .brand {
    position: absolute; left: 70px; top: 58px; width: 420px;
    font-size: 28px;
  }
  .card-front .brand-square { width: 22px; height: 22px; }

  .web-pill {
    position: absolute; left: 40px; top: 218px;
    background: var(--brand-blue); color: var(--white);
    border-radius: 6px;
    padding: 7px 12px;
    font-size: 12px; font-weight: 600; letter-spacing: 0.6px;
    white-space: nowrap;
  }
  .contact-list {
    position: absolute; left: 262px; top: 190px;
    border-left: 1.5px solid var(--brand-blue);
    padding: 4px 0 22px 12px;
    list-style: none;
  }
  .contact-item {
    display: flex; align-items: center; gap: 6px;
    font-size: 11px; margin-bottom: 8px;
    white-space: nowrap;
  }
  .contact-item.phone { font-size: 15px; }
  .contact-icon { width: 12px; height: 12px; flex: none; }

  /* Back */
  .card-back .brand {
    position: absolute; left: 50px; top: 40px; width: 450px;
    font-size: 31px;
  }
  .card-back .brand-square { width: 26px; height: 26px; }
  .services-title {
    position: absolute; left: 58px; top: 150px;
    color: var(--brand-blue);
    font-size: 21px; font-weight: 600; letter-spacing: 6px;
  }
  .services-list {
    position: absolute; left: 58px; top: 192px;
    list-style: none;
    font-size: 17px; font-weight: 600; line-height: 1.5;
  }
  .services-list .row { display: flex; gap: 22px; padding-left: 80px; }
</style>
</head>
<body>
<main class="sheet">

  <section class="card card-front" aria-label="Business card front">
    <div class="brand">
      <span class="brand-square"></span>
      <span class="brand-name">Brightway Haul &amp; Upkeep Services</span>
    </div>

    <div class="web-pill">www.brightwayhaul.com.au</div>

    <ul class="contact-list">
      <li class="contact-item phone">
        <svg class="contact-icon" viewBox="0 0 24 24" aria-hidden="true">
          <path fill="var(--brand-blue)" d="M6.6 10.8a15.1 15.1 0 0 0 6.6 6.6l2.2-2.2a1 1 0 0 1 1-.25 11.4 11.4 0 0 0 3.6.57 1 1 0 0 1 1 1V20a1 1 0 0 1-1 1A17 17 0 0 1 3 4a1 1 0 0 1 1-1h3.5a1 1 0 0 1 1 1c0 1.25.2 2.45.57 3.6a1 1 0 0 1-.25 1z"/>
        </svg>
        0487650392
      </li>
      <li class="contact-item email">
        <svg class="contact-icon" viewBox="0 0 24 24" aria-hidden="true">
          <rect x="2" y="5" width="20" height="14" rx="2" fill="var(--brand-blue)"/>
          <path d="M3 6l9 7 9-7" fill="none" stroke="var(--white)" stroke-width="2"/>
        </svg>
        brightwayhaulandupkeep@mailbox.example
      </li>
    </ul>
  </section>

  <section class="card card-back" aria-label="Business card back">
    <div class="brand">
      <span class="brand-square"></span>
      <span class="brand-name">Brightway Haul &amp; Upkeep Services</span>
    </div>

    <h2 class="services-title">Services we offer</h2>
    <ul class="services-list">
      <li class="row"><span>• Clean</span><span>• Move</span></li>
      <li>• General maintenance and repairs.</li>
    </ul>
  </section>

</main>
</body>
</html>
```